Automotive component supplier needs a business card design

We need a business card design for our company called Velran Global Components Ltd based in the UK. We are a supplier of interior and exterior components to premium car manufacturers such as Corvel Ashby, Hadley Fenn, Marquist and Tavarelli. We would like to see a modern business card design that uses the colour blue.

Target Market(s)

Premium automotive car manufacturers.

Industry/Entity Type

Automotive

Contact Information for Business Card

Company Name : Velran Global Components Limited
Address: 17 Marlow Yard, Upper Heath, Warwick, CV31 8QL, United Kingdom
Web Address : www.velrancomponents-example.co.uk

Font styles to use
Other font styles liked:
• Helvetica

Colors
3176b5
0255a3
85acd3
cfdeed
cee9f5
85cae6
34a6d7
0692cd
9bcb3c

Requirements
Must have
• Clear company logo and a mixture of blue colours.
Nice to have
• A high quality modern image.
Should not have
• Multiple colours.

```html
<!DOCTYPE html>
<html lang="en">
<head>
<meta charset="utf-8">
<title>Velran Global Components – Business Card</title>
<link rel="stylesheet" href="https://fonts.googleapis.com/css2?family=Arimo:wght@400;700&display=swap">
<style>
  :root {
    --brand-blue: #0692cd;
    --brand-blue-soft: #34a6d7;
    --brand-green: #9bcb3c;
    --card-white: #ffffff;
    --backdrop: #e9edf1;
    --ink-white: #ffffff;
  }
  * { box-sizing: border-box; margin: 0; padding: 0; }
  html, body {
    width: 1200px; height: 900px; overflow: hidden;
    background: var(--backdrop);
    font-family: "Arimo", Helvetica, Arial, sans-serif;
  }
  .canvas { position: relative; width: 1200px; height: 900px; }

  .card {
    position: absolute; width: 560px; height: 320px; overflow: hidden;
    box-shadow: 0 10px 28px rgba(20, 40, 70, 0.18);
  }

  /* Front */
  .card-front { left: 90px; top: 90px; background: var(--brand-blue); }
  .front-texture {
    position: absolute; inset: 0;
    background: linear-gradient(135deg, var(--brand-blue-soft) 0%, var(--brand-blue) 100%);
    opacity: 0.9;
  }
  .front-brand {
    position: absolute; right: 60px; top: 150px;
    display: flex; align-items: center; gap: 10px;
  }
  .brand-dot { width: 12px; height: 12px; background: var(--brand-green); flex: none; }
  .brand-name {
    font-weight: 700; font-size: 30px; letter-spacing: 0.5px; line-height: 1.05;
  }
  .front-brand .brand-name { color: var(--ink-white); }

  /* Back */
  .card-back { left: 550px; top: 490px; background: var(--card-white); }
  .back-swoosh { position: absolute; inset: 0; }
  .back-brand {
    position: absolute; left: 32px; top: 36px;
    display: flex; align-items: center; gap: 10px;
  }
  .back-brand .brand-name { color: var(--brand-blue); }
  .contact-list {
    position: absolute; left: 40px; bottom: 20px; list-style: none;
    color: var(--ink-white); font-size: 15px; line-height: 19px;
  }
  .contact-list li { display: flex; align-items: center; gap: 8px; }
  .contact-list svg { width: 11px; height: 11px; flex: none; }
  .address {
    position: absolute; right: 26px; top: 150px; text-align: right;
    color: var(--ink-white); font-size: 15px; line-height: 19px; font-style: normal;
  }
</style>
</head>
<body>
<main class="canvas">

  <section class="card card-front" aria-label="Business card front">
    <div class="front-texture" role="img" aria-label="Repeating brand pattern in tonal blue"></div>
    <div class="front-brand">
      <span class="brand-dot"></span>
      <span class="brand-name">Velran<br>Global Components</span>
    </div>
  </section>

  <section class="card card-back" aria-label="Business card back">
    <svg class="back-swoosh" viewBox="0 0 560 320" preserveAspectRatio="none" aria-hidden="true">
      <path d="M0,178 Q290,92 560,80 L560,92 Q300,104 0,202 Z" fill="var(--brand-green)"/>
      <path d="M0,206 Q300,110 560,96 L560,320 L0,320 Z" fill="var(--brand-blue)"/>
    </svg>

    <div class="back-brand">
      <span class="brand-dot"></span>
      <span class="brand-name">Velran<br>Global Components</span>
    </div>

    <address class="address">
      17 Marlow Yard, Upper Heath<br>
      Warwick, CV31 8QL, UK
    </address>

    <ul class="contact-list">
      <li>
        <svg viewBox="0 0 12 12"><path d="M2.5 1 L4.5 1 L5.2 3.5 L4 4.5 Q5 7 7.5 8 L8.5 6.8 L11 7.5 L11 9.5 Q10 11 8 10.8 Q2 9.5 1 3.5 Q1 1.5 2.5 1 Z" fill="var(--brand-green)"/></svg>
        780 612-4410
      </li>
      <li>
        <svg viewBox="0 0 12 12"><rect x="3" y="0.5" width="6" height="11" rx="1" fill="none" stroke="var(--brand-green)" stroke-width="1.2"/><circle cx="6" cy="9.5" r="0.7" fill="var(--brand-green)"/></svg>
        780 612-4478
      </li>
      <li>
        <svg viewBox="0 0 12 12"><rect x="0.5" y="2.5" width="11" height="7" fill="var(--brand-green)"/><path d="M0.5 2.5 L6 6.5 L11.5 2.5" fill="none" stroke="var(--brand-blue)" stroke-width="1"/></svg>
        velranparts@example.com
      </li>
      <li>
        <svg viewBox="0 0 12 12"><circle cx="6" cy="6" r="5.2" fill="none" stroke="var(--brand-green)" stroke-width="1.2"/><path d="M0.8 6 H11.2 M6 0.8 Q3 6 6 11.2 M6 0.8 Q9 6 6 11.2" fill="none" stroke="var(--brand-green)" stroke-width="0.9"/></svg>
        www.velrancomponents-example.co.uk
      </li>
    </ul>
  </section>

</main>
</body>
</html>
```